Australian Trucking Company Requires Professional Looking Stationary

We require a professional looking stationary design that incorporates our newly designed logo.

Our business, called "Brell Haulage Contracting", provides contracting work, transport and logistics to business in Western Australia particularly with links to the mining sector.

We are a small business looking to expand and our new logo and our new stationary will help develop our brand image in our market place.

Target Market(s)

Businesses and Corporation with links to the Mining Sector

Industry/Entity Type

Small Business

Requirements
Must have
• The letterhead must have the following details:
The new logo

Text saying: "Brell Holdings Pty Ltd (ACN 582 316 907) ATF The Brell Discretionary Trust T/AS"
"ABN 71 834 209 553"
Address "P.O Box 817 Wattlegrove WA, 6958"
Phone: 08 9352 7140
Email: brellhaul@mailbox-example.com.au

The text on the letterhead should be editable as the details are likely to change in the near future. Provision should be made for a website address all though one isn't available at the moment.

The styling, layout and font text is entirely up to the designer.

```html
<!DOCTYPE html>
<html lang="en">
<head>
<meta charset="utf-8">
<title>Brell Haulage Contracting – Business Card</title>
<link href="https://fonts.googleapis.com/css2?family=Open+Sans:wght@400;600;700&display=swap" rel="stylesheet">
<style>
  :root {
    --backdrop: #e9e6e2;
    --card-white: #ffffff;
    --brand-red: #e31b23;
    --brand-red-dark: #b8151c;
    --brand-red-light: #ef3a3f;
    --logo-red: #a3151b;
    --text-light: #ffffff;
    --shadow: rgba(0, 0, 0, 0.28);
  }
  * { box-sizing: border-box; margin: 0; padding: 0; }
  html, body { width: 1200px; height: 650px; overflow: hidden; }
  body {
    background: var(--backdrop);
    font-family: "Open Sans", Arial, sans-serif;
    position: relative;
  }
  .card {
    position: absolute;
    top: 170px;
    width: 540px;
    height: 310px;
    border-radius: 28px;
    overflow: hidden;
    box-shadow: 0 10px 24px var(--shadow);
  }
  .card--front { left: 40px; display: flex; }
  .card--back {
    left: 620px;
    background: linear-gradient(160deg, var(--brand-red-dark) 0%, var(--brand-red) 45%, var(--brand-red) 100%);
  }

  /* Front: logo side */
  .front__brand {
    width: 290px;
    background: var(--card-white);
    display: flex;
    align-items: center;
    justify-content: center;
    gap: 12px;
    padding: 0 22px;
  }
  .brand__dot {
    width: 34px; height: 34px;
    border-radius: 50%;
    background: var(--logo-red);
    flex: none;
  }
  .brand__name {
    color: var(--logo-red);
    font-weight: 700;
    font-size: 21px;
    line-height: 1.05;
    text-transform: uppercase;
  }

  /* Front: details side */
  .front__details {
    flex: 1;
    background: linear-gradient(170deg, var(--brand-red-dark) 0%, var(--brand-red) 40%, var(--brand-red) 100%);
    color: var(--text-light);
    padding: 44px 18px 26px 22px;
    display: flex;
    flex-direction: column;
  }
  .person { font-size: 17px; font-weight: 700; margin-bottom: 18px; }
  .person__title { font-size: 10px; font-weight: 400; }
  .contact-list { list-style: none; }
  .contact-list li {
    display: flex;
    align-items: flex-start;
    gap: 6px;
    font-size: 12px;
    line-height: 1.35;
    margin-bottom: 4px;
  }
  .contact-list svg { width: 11px; height: 11px; flex: none; margin-top: 3px; fill: var(--text-light); }
  .contact-list .address { margin-top: 6px; }
  .abn { margin-top: auto; font-size: 12px; letter-spacing: 0.3px; }

  /* Back */
  .back__artwork {
    position: absolute;
    left: 110px; top: 36px;
    width: 320px; height: 200px;
    border-radius: 14px;
    background: radial-gradient(ellipse at center, var(--brand-red-light) 0%, var(--brand-red) 75%);
  }
  .back__legal {
    position: absolute;
    left: 0; right: 0; bottom: 26px;
    text-align: center;
    color: var(--text-light);
    font-size: 11.5px;
  }
</style>
</head>
<body>

  <section class="card card--front">
    <div class="front__brand">
      <span class="brand__dot"></span>
      <span class="brand__name">Brell<br>Haulage<br>Contracting</span>
    </div>
    <div class="front__details">
      <p class="person">Your Name, <span class="person__title">Title</span></p>
      <ul class="contact-list">
        <li>
          <svg viewBox="0 0 24 24"><path d="M6.6 10.8a15.1 15.1 0 0 0 6.6 6.6l2.2-2.2c.3-.3.7-.4 1-.2 1.1.4 2.3.6 3.6.6.6 0 1 .4 1 1V20c0 .6-.4 1-1 1C10.6 21 3 13.4 3 4c0-.6.4-1 1-1h3.5c.6 0 1 .4 1 1 0 1.3.2 2.5.6 3.6.1.3 0 .7-.2 1z"/></svg>
          <span>08 9352 7140</span>
        </li>
        <li>
          <svg viewBox="0 0 24 24"><path d="M2 5h20v14H2z M2 5l10 8 10-8" /><path d="M3 6l9 7 9-7v1l-9 7-9-7z" fill="#e31b23"/></svg>
          <span>brellhaul@mailbox-example.com.au</span>
        </li>
        <li>
          <svg viewBox="0 0 24 24"><path d="M12 2a10 10 0 1 0 0 20 10 10 0 0 0 0-20zm0 2c.9 1.2 1.6 2.8 1.9 5H10.1C10.4 6.8 11.1 5.2 12 4zM4.3 13a8 8 0 0 1 0-2h3.8a17 17 0 0 0 0 2zm.8 2h3.2c.3 1.6.8 3 1.5 4.2A8 8 0 0 1 5.1 15zm3.2-6H5.1a8 8 0 0 1 4.7-4.2C9.1 6 8.6 7.4 8.3 9zM12 20c-.9-1.2-1.6-2.8-1.9-5h3.8c-.3 2.2-1 3.8-1.9 5zm2.1-7h-4.2a15 15 0 0 1 0-2h4.2a15 15 0 0 1 0 2zm.1 6.2c.7-1.2 1.2-2.6 1.5-4.2h3.2a8 8 0 0 1-4.7 4.2zM15.9 13a17 17 0 0 0 0-2h3.8a8 8 0 0 1 0 2zm-.2-4c-.3-1.6-.8-3-1.5-4.2A8 8 0 0 1 18.9 9z"/></svg>
          <span>www.brellhaulage.com.au</span>
        </li>
        <li class="address">
          <svg viewBox="0 0 24 24"><path d="M12 3l10 9h-3v9h-5v-6h-4v6H5v-9H2z"/></svg>
          <span>P.O Box 817<br>Wattlegrove WA, 6958</span>
        </li>
      </ul>
      <p class="abn">ABN 71 834 209 553</p>
    </div>
  </section>

  <section class="card card--back">
    <div class="back__artwork" role="img" aria-label="Large white illustration of a prime mover truck driving forward on a curved road"></div>
    <p class="back__legal">Brell Holdings Pty Ltd (ACN 582 316 907) ATF The Brell Discretionary Trust T/AS</p>
  </section>

</body>
</html>
```